Business Card for a Dental Office

The design should communicate integrity, quality and reliability. We also want the card look elegant, simple, but still stand out, different from the traditional-dental-office business card.

Industry/Entity Type

Business

```html
<!DOCTYPE html>
<html lang="en">
<head>
<meta charset="utf-8">
<title>Harlow Dental Centre – Business Card</title>
<link rel="stylesheet" href="https://fonts.googleapis.com/css2?family=Oswald:wght@500;600&family=Open+Sans:wght@400;600&display=swap">
<style>
  :root {
    --backdrop: #e9e6df;
    --card-black: #0b0b0b;
    --card-sheen: #1c1c1c;
    --gold: #e2dc2a;
    --gold-muted: #b9a24a;
    --gold-faint: rgba(170, 150, 60, 0.16);
    --white: #f4f4f4;
    --grey: #8d8d8d;
  }
  * { margin: 0; padding: 0; box-sizing: border-box; }
  html, body { width: 1200px; height: 1022px; overflow: hidden; }
  body {
    background: var(--backdrop);
    font-family: "Open Sans", Arial, sans-serif;
    position: relative;
  }
  .card {
    position: absolute;
    left: 150px; top: 254px;
    width: 900px; height: 514px;
    border-radius: 26px;
    background: linear-gradient(135deg, var(--card-sheen) 0%, var(--card-black) 45%, var(--card-black) 100%);
    box-shadow: 0 18px 40px rgba(0,0,0,0.35);
    overflow: hidden;
  }
  .card__watermark {
    position: absolute;
    left: 380px; top: 120px;
    width: 300px; height: 300px;
    background: var(--gold-faint);
  }
  .brand {
    position: absolute;
    left: 64px; top: 70px;
    display: flex; align-items: center; gap: 26px;
  }
  .brand__mark {
    width: 104px; height: 104px;
    background: var(--gold);
  }
  .brand__name {
    font-family: "Oswald", "Arial Narrow", sans-serif;
    font-weight: 600;
    font-size: 50px;
    line-height: 1;
    letter-spacing: 0.5px;
    color: var(--white);
    text-transform: uppercase;
  }
  .brand__tagline {
    margin-top: 10px;
    font-family: "Oswald", "Arial Narrow", sans-serif;
    font-weight: 500;
    font-size: 24px;
    letter-spacing: 1px;
    color: var(--gold);
    text-transform: uppercase;
  }
  .brand__tagline-lead { color: var(--gold-muted); }
  .person {
    position: absolute;
    left: 64px; top: 372px;
  }
  .person__name {
    font-family: "Oswald", "Arial Narrow", sans-serif;
    font-weight: 600;
    font-size: 38px;
    line-height: 1.1;
    color: var(--gold);
    text-transform: uppercase;
  }
  .person__title {
    font-size: 20px;
    letter-spacing: 2px;
    color: var(--grey);
    text-transform: uppercase;
  }
  .divider {
    position: absolute;
    left: 372px; top: 356px;
    width: 2px; height: 108px;
    background: var(--gold-muted);
  }
  .contact {
    position: absolute;
    left: 396px; top: 358px;
    list-style: none;
  }
  .contact__item {
    display: flex; align-items: center; gap: 14px;
    font-size: 21px;
    line-height: 34px;
    color: var(--gold);
  }
  .contact__icon { width: 18px; height: 18px; flex: none; }
</style>
</head>
<body>
  <section class="card" aria-label="Harlow Dental Centre business card">
    <div class="card__watermark" aria-hidden="true"></div>

    <header class="brand">
      <div class="brand__mark" aria-hidden="true"></div>
      <div class="brand__text">
        <h1 class="brand__name">Harlow Dental Centre</h1>
        <p class="brand__tagline"><span class="brand__tagline-lead">Your smile is</span> your gift to others</p>
      </div>
    </header>

    <div class="person">
      <p class="person__name">Mara Ellison</p>
      <p class="person__title">Director</p>
    </div>

    <div class="divider" aria-hidden="true"></div>

    <ul class="contact">
      <li class="contact__item">
        <svg class="contact__icon" viewBox="0 0 24 24" aria-hidden="true"><path fill="#b9a24a" d="M6.6 10.8a15 15 0 0 0 6.6 6.6l2.2-2.2c.3-.3.7-.4 1-.2 1.1.4 2.3.6 3.6.6.6 0 1 .4 1 1V20c0 .6-.4 1-1 1A17 17 0 0 1 3 4c0-.6.4-1 1-1h3.5c.6 0 1 .4 1 1 0 1.3.2 2.5.6 3.6.1.3 0 .7-.2 1z"/></svg>
        +330 2460-5190
      </li>
      <li class="contact__item">
        <svg class="contact__icon" viewBox="0 0 24 24" aria-hidden="true"><rect x="3" y="5" width="18" height="14" fill="none" stroke="#b9a24a" stroke-width="2"/><path d="M3 6l9 7 9-7" fill="none" stroke="#b9a24a" stroke-width="2"/></svg>
        info@harlowdentalcentre.com
      </li>
      <li class="contact__item">
        <svg class="contact__icon" viewBox="0 0 24 24" aria-hidden="true"><g fill="none" stroke="#b9a24a" stroke-width="2"><circle cx="12" cy="12" r="9"/><ellipse cx="12" cy="12" rx="4" ry="9"/><path d="M3 12h18"/></g></svg>
        www.harlowdentalcentre.com
      </li>
    </ul>
  </section>
</body>
</html>
```